BUSINESS CARD - HALLORAN FIELD SERVICES

I would like to create a business card for my fertilizer spreading business. I would like to incorporate my existing logo and also a description of the services offered. The business card will be given to farmers so must be kept simple but effective. It will also be left in stores so much also be eye catching in order to stand out from other cards.

Target Market(s)

FARMERS

Requirements
Must have
• FRONT OF CARD = EXISTING LOGO + "CUSTOMISED SPREADING" below the logo

REAR Of CARD = SERVICES OFFERED AND CONTACT DETAILS

- Bulk fertilizer including Lime, Gypsum, Manure & Compost
- Granular fertilizer including Single Super, Urea, Gran-Sul, & Custom Blends
- Modern equipment - Autosteer & Variable Rate Capable
- Friendly & Reliable Service
- Contact Gus: 0417 552 308
Nice to have
• utilize same color scheme as existing logo

```html
<!DOCTYPE html>
<html lang="en">
<head>
<meta charset="utf-8">
<title>Halloran Field Services – Business Card</title>
<link href="https://fonts.googleapis.com/css2?family=Lato:ital,wght@0,400;0,700;0,900;1,400&display=swap" rel="stylesheet">
<style>
  :root {
    --page-bg: #8a8b8d;
    --card-white: #ffffff;
    --charcoal: #58585a;
    --charcoal-deep: #4c4c4e;
    --orange: #f7941d;
    --pale-grey: #ececec;
    --light-text: #f2f2f2;
  }
  * { margin: 0; padding: 0; box-sizing: border-box; }
  html, body {
    width: 1200px; height: 1200px; overflow: hidden;
    background: var(--page-bg);
    font-family: "Lato", Arial, sans-serif;
  }
  .card {
    position: absolute; left: 184px; width: 840px; height: 488px; overflow: hidden;
  }
  /* Front */
  .card--front { top: 94px; background: var(--card-white); }
  .front__plant {
    position: absolute; top: 50px; width: 170px; height: 370px;
    background: linear-gradient(180deg, rgba(236,236,236,0.9), rgba(236,236,236,0.4));
    border-radius: 50% 50% 8px 8px;
  }
  .front__plant--left { left: 50px; }
  .front__plant--right { right: 50px; }
  .brand {
    position: absolute; left: 0; right: 0; top: 40px;
    display: flex; flex-direction: column; align-items: center;
  }
  .brand__mark {
    width: 150px; height: 150px; border-radius: 50%; background: var(--charcoal);
  }
  .brand__name {
    margin-top: 30px; font-weight: 900; font-size: 48px; letter-spacing: 1px;
    color: var(--charcoal); white-space: nowrap;
  }
  .front__band {
    position: absolute; left: 0; right: 0; bottom: 0; height: 80px;
    background: var(--orange); color: var(--card-white);
    display: flex; align-items: center; justify-content: center;
    font-weight: 700; font-size: 44px; letter-spacing: 0.5px;
  }
  /* Back */
  .card--back { top: 630px; background: var(--charcoal); }
  .back__motif {
    position: absolute; left: 20px; top: 20px; width: 620px; height: 470px;
    border-radius: 50%;
    background: radial-gradient(circle at 60% 40%, rgba(255,255,255,0.07), rgba(255,255,255,0) 70%);
  }
  .back__brand {
    position: absolute; right: 26px; top: 34px;
    display: flex; flex-direction: column; align-items: center;
  }
  .back__brand-mark { width: 52px; height: 52px; border-radius: 50%; background: var(--light-text); }
  .back__brand-name {
    margin-top: 8px; font-weight: 700; font-size: 15px; color: var(--light-text);
    letter-spacing: 0.5px; white-space: nowrap;
  }
  .services {
    position: absolute; left: 176px; top: 168px; list-style: none;
    color: var(--light-text); font-size: 19px; line-height: 26px;
  }
  .services__item { position: relative; padding-left: 36px; margin-bottom: 8px; }
  .services__bullet { position: absolute; left: 0; top: 7px; width: 22px; height: 12px; }
  .services__title { color: var(--orange); font-weight: 700; text-transform: uppercase; }
  .services__title em { color: var(--light-text); font-weight: 400; text-transform: none; }
  .back__band {
    position: absolute; left: 0; right: 0; bottom: 0; height: 60px;
    background: var(--orange); display: flex; align-items: center; padding-left: 160px;
  }
  .contact__icon { width: 40px; height: 40px; margin-right: 18px; }
  .contact__text { color: var(--card-white); font-weight: 700; font-size: 33px; }
</style>
</head>
<body>
  <section class="card card--front">
    <div class="front__plant front__plant--left" role="img" aria-label="Faint grain stalk illustration"></div>
    <div class="front__plant front__plant--right" role="img" aria-label="Faint grain stalk illustration"></div>
    <div class="brand">
      <div class="brand__mark"></div>
      <div class="brand__name">HALLORAN FIELD SERVICES</div>
    </div>
    <div class="front__band">CUSTOMISED SPREADING</div>
  </section>

  <section class="card card--back">
    <div class="back__motif" role="img" aria-label="Faint decorative crop motif"></div>
    <div class="back__brand">
      <div class="back__brand-mark"></div>
      <div class="back__brand-name">HALLORAN FIELD SERVICES</div>
    </div>
    <ul class="services">
      <li class="services__item">
        <svg class="services__bullet" viewBox="0 0 22 12"><path d="M0 0 L11 12 L22 0 Z" fill="#f7941d"/></svg>
        <span class="services__title">Bulk Fertilizer <em><i>including</i></em></span><br>
        Lime, Gypsum, Manure &amp; Compost
      </li>
      <li class="services__item">
        <svg class="services__bullet" viewBox="0 0 22 12"><path d="M0 0 L11 12 L22 0 Z" fill="#f7941d"/></svg>
        <span class="services__title">Modern Equipment</span><br>
        Autosteer &amp; Variable Rate Capable
      </li>
      <li class="services__item">
        <svg class="services__bullet" viewBox="0 0 22 12"><path d="M0 0 L11 12 L22 0 Z" fill="#f7941d"/></svg>
        <span class="services__title">Granular Fertilizer <em><i>including</i></em></span><br>
        Single Super, Urea, Gran-Sul,<br>and Custom Blends
      </li>
      <li class="services__item">
        <svg class="services__bullet" viewBox="0 0 22 12"><path d="M0 0 L11 12 L22 0 Z" fill="#f7941d"/></svg>
        <span class="services__title">Friendly &amp; Reliable Services</span>
      </li>
    </ul>
    <div class="back__band">
      <svg class="contact__icon" viewBox="0 0 40 40" aria-hidden="true">
        <circle cx="20" cy="20" r="20" fill="#58585a"/>
        <path d="M14 11 c1.5-1 3 0 4 2 l1 2.5 c0.5 1.2-0.5 2-1.5 2.8 c1 2.5 3 4.5 5.5 5.5 c0.8-1 1.6-2 2.8-1.5 l2.5 1 c2 1 3 2.5 2 4 c-1.5 2.5-4 3-7 1.7 c-5-2.2-9-6.2-11-11 c-1.2-3 -0.7-5.5 1.7-7 Z" fill="#ffffff"/>
      </svg>
      <span class="contact__text">GUS: 0417 552 308</span>
    </div>
  </section>
</body>
</html>
```